Core values in our company OKV (Residency and Relocation)

Do good:
1. Being Direct and communicative for the benefit of all parties
2. Working for the Benefit of the company, client and team members
3. Wanting to improve to create a better impact
4. Having healthy rivalry
Be ahead of curve:
1. Having the confidence to break through barriers which arise
2. Desire to grow and learn towards establishment and agreed goal
3. Getting off the sidelines and get into the game
4. Keeping the end game in mind having due regard to processes and milestones
5. Self starter and works on own initiative
6. Diligent and impactful in your field of responsibility
Truth and Honesty
2. Have the confidence and ability to speak what you really want to communicate
3. Being truthful to yourself, clients and colleagues to find the innovations that lie within
4. Seeking the truth by opening things up for discussion
5. Being Optimistic
Background Information on our Company:OKV is a professional law firm in London Docklands. We caters for both private and corporate clients ranging from highly regarded and established law firms to boutique and niche immigration practices. We also specialises in expert legal advice and prides itself on providing services that go beyond the expectations of its clients.
What we need: We need a Poster about Truth and Honesty, this is to show one of our values as a company. It will need to be vibrant and straight to the point. Colours can be orange grey white and yellow. Attached is our company logo.
Reason: To remind colleagues that this is one of our main values and it is instilled in our company.
Things we would like:
1. To create a point of focus
2. Use shapes to create visual interest
3. Use creative illustrations
4. Take the viewer’s focus on a journey with clever perspective
Industry/Entity Type
Legal
Requirements
Must have
- a globe (Picture)
- Do good:
- 1. Being Direct and communicative for the benefit of all parties
- 2. Working for the Benefit of the company, client and team members
- 3. Wanting to improve to create a better impact
- 4. Having healthy rivalry
- Be ahead of curve:
- 1. Having the confidence to break through barriers which arise
- 2. Desire to grow and learn towards establishment and agreed goal
- 3. Getting off the sidelines and get into the game
- 4. Keeping the end game in mind having due regard to processes and milestones
- 5. Self starter and works on own initiative
- 6. Diligent and impactful in your field of responsibility
- Truth and Honesty
- 2. Have the confidence and ability to speak what you really want to communicate
- 3. Being truthful to yourself, clients and colleagues to find the innovations that lie within
- 4. Seeking the truth by opening things up for discussion
- 5. Being Optimistic

```html
<!DOCTYPE html>
<html lang="en">
<head>
<meta charset="utf-8">
<title>OKV Core Values Poster Options</title>
<link rel="stylesheet" href="https://fonts.googleapis.com/css2?family=Archivo+Black&family=Oswald:wght@400;500&family=Roboto+Condensed:wght@400;700&family=Crimson+Text&display=swap">
<style>
  :root {
    --board: #fbe7b4;
    --cream: #fdf7df;
    --cream-deep: #f8e6b0;
    --orange: #f7941d;
    --yellow: #f5b81c;
    --charcoal: #3b3a39;
    --ink: #1f1d1b;
    --space-dark: #2a1a0e;
    --space-warm: #a35a16;
    --space-grey: #3a3938;
  }
  * { margin: 0; padding: 0; box-sizing: border-box; }
  html, body { width: 1200px; height: 635px; overflow: hidden; }
  body {
    background: var(--board);
    position: relative;
    font-family: "Roboto Condensed", "Arial Narrow", sans-serif;
    color: var(--ink);
  }
  .poster {
    position: absolute;
    top: 84px;
    width: 337px;
    height: 478px;
    overflow: hidden;
    box-shadow: 0 6px 14px rgba(60, 40, 10, 0.45);
    background: linear-gradient(180deg, var(--cream-deep) 0%, var(--cream) 45%, #fffdf4 100%);
  }
  .poster--one { left: 62px; }
  .poster--two { left: 423px; }
  .poster--three { left: 790px; background: linear-gradient(180deg, #fbe6a6 0%, var(--cream) 60%, #fffbee 100%); }

  .option-label {
    position: absolute;
    top: 578px;
    width: 337px;
    text-align: center;
    font-family: "Archivo Black", "Arial Black", sans-serif;
    font-size: 33px;
    letter-spacing: 1px;
    color: #000;
  }

  /* brand block */
  .brand { position: absolute; text-align: center; }
  .brand__name {
    display: inline-flex; align-items: center; gap: 5px;
    font-family: "Roboto Condensed", sans-serif; font-weight: 700;
    font-size: 36px; line-height: 1; color: var(--charcoal);
  }
  .brand__mark { width: 9px; height: 9px; background: var(--orange); }
  .brand__tagline {
    font-family: "Crimson Text", Georgia, serif;
    font-size: 9px; color: #4a4540; margin-top: 3px;
  }

  /* split layout (options 1 & 2) */
  .artwork { position: absolute; }
  .split .artwork { left: 199px; top: 0; width: 138px; height: 478px; }
  .artwork--warm {
    background: linear-gradient(180deg, #2b1a0d 0%, #8a4a16 22%, #3a230f 40%, #7a4a22 58%, #2e1c0e 74%, #b0702e 90%, #2a180c 100%);
  }
  .artwork--mixed {
    background: linear-gradient(180deg, #1c1510 0%, #6e665c 22%, #2a1e14 40%, #6a4520 58%, #1e1610 74%, #8d8a85 90%, #1a1612 100%);
  }

  .value { position: absolute; left: 21px; width: 175px; }
  .tag {
    display: inline-block; position: relative;
    font-family: "Oswald", sans-serif; font-weight: 500;
    font-size: 13px; line-height: 17px; padding: 0 5px;
    border-radius: 4px; color: #fff; margin-left: 6px;
  }
  .tag::after {
    content: ""; position: absolute; left: 8px; bottom: -4px;
    border-left: 4px solid transparent; border-right: 4px solid transparent;
    border-top: 4px solid transparent;
  }
  .tag--orange { background: var(--orange); }
  .tag--orange::after { border-top-color: var(--orange); }
  .tag--yellow { background: var(--yellow); }
  .tag--yellow::after { border-top-color: var(--yellow); }
  .tag--dark { background: var(--charcoal); }
  .tag--dark::after { border-top-color: var(--charcoal); }

  .timeline { list-style: none; position: relative; margin-top: 5px; padding-left: 11px; }
  .timeline::before {
    content: ""; position: absolute; left: 2px; top: 3px; bottom: 4px;
    width: 1px; background: var(--line);
  }
  .timeline li, .checklist li {
    position: relative; font-size: 7.3px; line-height: 9.4px;
    font-weight: 700; margin-bottom: 3.7px; color: var(--ink);
  }
  .timeline li::before {
    content: ""; position: absolute; left: -11px; top: 2px;
    width: 5px; height: 5px; background: var(--line);
  }
  .timeline--orange { --line: var(--orange); }
  .timeline--yellow { --line: var(--yellow); }
  .timeline--dark { --line: var(--charcoal); }

  /* grid layout (option 3) */
  .grid .artwork--saturn { left: 183px; top: 0; width: 154px; height: 171px;
    background: linear-gradient(160deg, #3a220e 0%, #9a5a1e 45%, #5a3414 70%, #2a180c 100%); }
  .grid .artwork--astronaut { left: 0; top: 181px; width: 165px; height: 146px;
    background: linear-gradient(150deg, #2a2014 0%, #8a6a2e 45%, #c9a050 60%, #3a2c16 85%, #1e170f 100%); }
  .grid .artwork--earth { left: 183px; top: 352px; width: 154px; height: 126px;
    background: linear-gradient(135deg, #1b1b1b 0%, #7e7d7b 40%, #c8c7c4 55%, #3a3938 80%, #161616 100%); }

  .block { position: absolute; }
  .heading {
    font-family: "Oswald", sans-serif; font-weight: 500;
    font-size: 14px; line-height: 17px; padding-bottom: 2px;
    border-bottom: 2px solid var(--rule);
  }
  .heading--orange { color: var(--orange); --rule: var(--orange); }
  .heading--yellow { color: var(--yellow); --rule: var(--yellow); }
  .heading--dark { color: var(--charcoal); --rule: var(--charcoal); }
  .checklist { list-style: none; margin-top: 5px; padding-left: 14px; }
  .checklist li { font-weight: 400; color: #333; margin-bottom: 3.5px; }
  .checklist li::before {
    content: ""; position: absolute; left: -12px; top: 2px;
    width: 5px; height: 5px; background: var(--dot);
  }
  .checklist--orange { --dot: var(--orange); }
  .checklist--yellow { --dot: var(--yellow); }
  .checklist--dark { --dot: var(--charcoal); }
</style>
</head>
<body>

<section class="poster poster--one split">
  <div class="brand" style="left:40px; top:22px; width:150px;">
    <div class="brand__name">OKV<span class="brand__mark"></span></div>
    <div class="brand__tagline">Residency and Relocation</div>
  </div>
  <div class="value" style="top:105px;">
    <span class="tag tag--orange">DO GOOD:</span>
    <ul class="timeline timeline--orange">
      <li>Being Direct and communicative for the benefit of all parties</li>
      <li>Working for the Benefit of the company, client and team members</li>
      <li>Wanting to improve to create a better impact</li>
      <li>Having healthy rivalry</li>
    </ul>
  </div>
  <div class="value" style="top:209px;">
    <span class="tag tag--yellow">Be a Head of Curve:</span>
    <ul class="timeline timeline--yellow">
      <li>Having the confidence to break through barriers which arise</li>
      <li>Desire to grow and learn towards establishment and agreed goal</li>
      <li>Getting off the sidelines and get into the game</li>
      <li>Keeping the end game in mind having due regard to processes and milestones</li>
      <li>Self starter and works on own initiative</li>
      <li>Diligent and impactful in your field of responsibility</li>
    </ul>
  </div>
  <div class="value" style="top:348px;">
    <span class="tag tag--dark">Truth and Honesty</span>
    <ul class="timeline timeline--dark">
      <li>Having the confidence to break through barriers which arise</li>
      <li>Have the confidence and ability to speak what you really want to communicate</li>
      <li>Being truthful to yourself, clients and colleagues to find the innovations that lie within</li>
      <li>Seeking the truth by opening things up for discussion</li>
      <li>Being Optimistic</li>
    </ul>
  </div>
  <div class="artwork artwork--warm" role="img" aria-label="Warm orange space scene with a ringed planet, a floating astronaut and the globe of the Earth with its moon"></div>
</section>
<div class="option-label" style="left:62px;">OPTION 01</div>

<section class="poster poster--two split">
  <div class="brand" style="left:40px; top:22px; width:150px;">
    <div class="brand__name">OKV<span class="brand__mark"></span></div>
    <div class="brand__tagline">Residency and Relocation</div>
  </div>
  <div class="value" style="top:105px;">
    <span class="tag tag--orange">DO GOOD:</span>
    <ul class="timeline timeline--orange">
      <li>Being Direct and communicative for the benefit of all parties</li>
      <li>Working for the Benefit of the company, client and team members</li>
      <li>Wanting to improve to create a better impact</li>
      <li>Having healthy rivalry</li>
    </ul>
  </div>
  <div class="value" style="top:209px;">
    <span class="tag tag--yellow">Be a Head of Curve:</span>
    <ul class="timeline timeline--yellow">
      <li>Having the confidence to break through barriers which arise</li>
      <li>Desire to grow and learn towards establishment and agreed goal</li>
      <li>Getting off the sidelines and get into the game</li>
      <li>Keeping the end game in mind having due regard to processes and milestones</li>
      <li>Self starter and works on own initiative</li>
      <li>Diligent and impactful in your field of responsibility</li>
    </ul>
  </div>
  <div class="value" style="top:348px;">
    <span class="tag tag--dark">Truth and Honesty</span>
    <ul class="timeline timeline--dark">
      <li>Having the confidence to break through barriers which arise</li>
      <li>Have the confidence and ability to speak what you really want to communicate</li>
      <li>Being truthful to yourself, clients and colleagues to find the innovations that lie within</li>
      <li>Seeking the truth by opening things up for discussion</li>
      <li>Being Optimistic</li>
    </ul>
  </div>
  <div class="artwork artwork--mixed" role="img" aria-label="Space scene with a grey ringed planet, a bronze-toned astronaut and a silver globe of the Earth with its moon"></div>
</section>
<div class="option-label" style="left:423px;">OPTION 02</div>

<section class="poster poster--three grid">
  <div class="brand" style="left:16px; top:12px; width:160px;">
    <div class="brand__name">OKV<span class="brand__mark"></span></div>
    <div class="brand__tagline">Residency and Relocation</div>
  </div>
  <div class="block" style="left:17px; top:82px; width:162px;">
    <div class="heading heading--orange">DO GOOD</div>
    <ul class="checklist checklist--orange">
      <li>Being Direct and communicative for the benefit of all parties</li>
      <li>Working for the Benefit of the company, client and team members</li>
      <li>Wanting to improve to create a better impact</li>
      <li>Having healthy rivalry</li>
    </ul>
  </div>
  <div class="artwork artwork--saturn" role="img" aria-label="Ringed planet glowing orange in deep space"></div>
  <div class="artwork artwork--astronaut" role="img" aria-label="Astronaut floating in golden-lit space"></div>
  <div class="block" style="left:173px; top:203px; width:164px;">
    <div class="heading heading--yellow">Be a Head of Curve</div>
    <ul class="checklist checklist--yellow">
      <li>Having the confidence to break through barriers which arise</li>
      <li>Desire to grow and learn towards establishment and agreed goal</li>
      <li>Getting off the sidelines and get into the game</li>
      <li>Keeping the end game in mind having due regard to processes and milestones</li>
      <li>Self starter and works on own initiative</li>
      <li>Diligent and impactful in your field of responsibility</li>
    </ul>
  </div>
  <div class="block" style="left:17px; top:331px; width:160px;">
    <div class="heading heading--dark">Truth and Honesty</div>
    <ul class="checklist checklist--dark">
      <li>Having the confidence to break through barriers which arise</li>
      <li>Have the confidence and ability to speak what you really want to communicate</li>
      <li>Being truthful to yourself, clients and colleagues to find the innovations that lie within</li>
      <li>Seeking the truth by opening things up for discussion</li>
      <li>Being Optimistic</li>
    </ul>
  </div>
  <div class="artwork artwork--earth" role="img" aria-label="Black and white globe of the Earth with its moon in space"></div>
</section>
<div class="option-label" style="left:790px;">OPTION 03</div>

</body>
</html>
```